Restyle corporate identity (+ logo) for a road construction company

We need a new logo and stationary design for our company VARNOK path. VARNOK path® increases the road base strength, while reducing major costs and time of road construction. Attached some examples of the current design.

Our wishes for the new logo:
- Business look
- Style sheet
- Modern

More information: www.varnokpath.example
Updates

Target Market(s)

Government

Industry/Entity Type

Construction

Requirements
Must have
• Logo (with road sign) + text

```html
<!DOCTYPE html>
<html lang="en">
<head>
<meta charset="utf-8">
<title>VARNOK path – Business Cards</title>
<link rel="stylesheet" href="https://fonts.googleapis.com/css2?family=Source+Sans+3:wght@400;600&display=swap">
<style>
  :root {
    --backdrop: #9b9b9b;
    --card-white: #eef0f2;
    --brand-blue: #1a7de0;
    --back-blue: #0b7ae0;
    --text-grey: #4a4a4a;
    --muted-grey: #8a8a8a;
    --white: #ffffff;
  }
  * { box-sizing: border-box; margin: 0; padding: 0; }
  html, body { width: 1105px; height: 1200px; overflow: hidden; }
  body {
    background: var(--backdrop);
    font-family: "Source Sans 3", "Segoe UI", Arial, sans-serif;
    position: relative;
  }
  .card {
    position: absolute;
    left: 182px;
    width: 746px;
    height: 427px;
    overflow: hidden;
  }
  /* Front */
  .card-front { top: 119px; background: var(--card-white); }
  .brand {
    position: absolute;
    top: 108px; left: 0; right: 0;
    display: flex; align-items: center; justify-content: center; gap: 18px;
  }
  .brand-square { width: 58px; height: 58px; background: var(--brand-blue); }
  .brand-name {
    font-size: 64px; font-weight: 600; letter-spacing: 2px;
    color: var(--brand-blue); line-height: 1;
  }
  .person {
    position: absolute; top: 284px; left: 42px; right: 42px;
    display: flex; align-items: center; gap: 10px;
  }
  .person .rule { flex: 1; height: 2px; background: var(--brand-blue); }
  .person-name { font-size: 25px; font-weight: 600; color: var(--brand-blue); letter-spacing: 0.5px; }
  .person-dash { font-size: 25px; font-weight: 600; color: var(--brand-blue); margin: 0 6px; }
  .person-role { font-size: 19px; color: var(--muted-grey); }
  .address {
    position: absolute; top: 325px; left: 0; right: 0;
    text-align: center; font-size: 19px; color: var(--text-grey);
  }
  .contacts {
    position: absolute; top: 357px; left: 0; right: 0;
    display: flex; justify-content: center; gap: 26px;
    font-size: 19px; color: var(--text-grey);
  }
  .contact { display: flex; align-items: center; gap: 7px; }
  .contact svg { width: 18px; height: 18px; fill: var(--brand-blue); }
  /* Back */
  .card-back { top: 637px; background: var(--back-blue); }
  .back-square {
    position: absolute; left: 188px; top: 24px;
    width: 370px; height: 370px;
    background: rgba(255,255,255,0.08);
  }
  .back-name {
    position: absolute; top: 136px; left: 0; right: 0;
    text-align: center; font-size: 72px; font-weight: 600;
    letter-spacing: 3px; color: var(--white); line-height: 1;
  }
  .back-url {
    position: absolute; top: 270px; left: 0; right: 0;
    text-align: center; font-size: 20px; letter-spacing: 2px; color: var(--white);
  }
</style>
</head>
<body>
  <section class="card card-front">
    <div class="brand">
      <span class="brand-square"></span>
      <span class="brand-name">VARNOK PATH</span>
    </div>
    <div class="person">
      <span class="rule"></span>
      <span class="person-name">DAAN VERHOEF</span>
      <span class="person-dash">-</span>
      <span class="person-role">CEO/Founder</span>
      <span class="rule"></span>
    </div>
    <p class="address">Kanaalweg 58, 3526 KL Utrecht, The Netherlands</p>
    <div class="contacts">
      <span class="contact">
        <svg viewBox="0 0 24 24" aria-hidden="true"><path d="M6.6 10.8a15.1 15.1 0 0 0 6.6 6.6l2.2-2.2a1 1 0 0 1 1-.25 11.4 11.4 0 0 0 3.6.57 1 1 0 0 1 1 1V20a1 1 0 0 1-1 1A17 17 0 0 1 3 4a1 1 0 0 1 1-1h3.5a1 1 0 0 1 1 1c0 1.25.2 2.45.57 3.57a1 1 0 0 1-.25 1z"/></svg>
        614 208 5937
      </span>
      <span class="contact">
        <svg viewBox="0 0 24 24" aria-hidden="true"><path d="M2 5h20v14H2z M2 5l10 8 10-8" fill="none" stroke="#1a7de0" stroke-width="2.4"/></svg>
        hello@varnokpath.example
      </span>
      <span class="contact">
        <svg viewBox="0 0 24 24" aria-hidden="true"><circle cx="12" cy="12" r="10"/><path d="M2 12h20M12 2c3 3 3 17 0 20M12 2c-3 3-3 17 0 20" fill="none" stroke="#eef0f2" stroke-width="1.5"/></svg>
        www.varnokpath.example
      </span>
    </div>
  </section>

  <section class="card card-back">
    <span class="back-square"></span>
    <div class="back-name">VARNOK PATH</div>
    <div class="back-url">www.varnokpath.example</div>
  </section>
</body>
</html>
```